New career and executive coaching business needs a business card design including logo

Company name: 'Bramblefield Growth Partners.' The aim of my coaching engagements is to help people improve their communication in the workplace and achieve their career goals. The process involves working with individuals to help them uncover their strengths and talents, then leverage those to improve their working lives. The Tarwick Inventory is the starting point to the process. I am after an exciting and interesting business card design (including logo)which is professional yet will still get people's attention.

Industry/Entity Type

Business

Contact Information for Business Card

Name: Malcolm Dervaney
Position: Owner
Address: 58 Quorrin Ct, Elmbridge Vic 3190
Phone: 0418923047
Website: bramblefieldgrowth.com.au
Email: malcolm@bgp.com.au

Colors
33a6d7
00a990
0355a3
3176b5

Requirements
Must have
• logo

```html
<!DOCTYPE html>
<html lang="en">
<head>
<meta charset="utf-8">
<title>Bramblefield Growth Partners – Business Card</title>
<link rel="stylesheet" href="https://fonts.googleapis.com/css2?family=Oswald:wght@500&family=Source+Sans+3:wght@400;600&display=swap">
<style>
  :root {
    --sky: #33a6d7;
    --teal: #00a990;
    --royal: #0355a3;
    --steel: #3176b5;
    --name-blue: #1a4fa0;
    --muted: #9a9a9a;
    --card-white: #ffffff;
    --stage-top: #2b2b2b;
    --stage-bottom: #050505;
  }
  * { margin: 0; padding: 0; box-sizing: border-box; }
  html, body { width: 1200px; height: 900px; overflow: hidden; }
  body {
    position: relative;
    background: linear-gradient(180deg, var(--stage-top) 0%, #161616 55%, var(--stage-bottom) 100%);
    font-family: "Source Sans 3", "Myriad Pro", Arial, sans-serif;
  }
  .card {
    position: absolute;
    top: 306px;
    height: 271px;
    border-radius: 10px;
  }
  .card--front { left: 149px; width: 439px; background: var(--card-white); }
  .card--back { left: 608px; width: 441px; background: var(--royal); }

  /* front: brand block */
  .front-brand {
    position: absolute;
    left: 44px;
    top: 58px;
    width: 154px;
    text-align: center;
  }
  .front-brand__dot {
    width: 96px; height: 96px;
    margin: 0 auto 12px;
    border-radius: 50%;
    background: var(--steel);
  }
  .front-brand__name {
    font-family: "Oswald", "Arial Narrow", sans-serif;
    font-weight: 500;
    font-size: 15px;
    line-height: 1.2;
    letter-spacing: 0.5px;
    color: var(--royal);
    text-transform: uppercase;
  }

  /* front: contact details */
  .contact {
    position: absolute;
    left: 221px;
    top: 66px;
    color: var(--muted);
    font-size: 12.5px;
    line-height: 15px;
  }
  .contact__name {
    font-weight: 600;
    font-size: 15px;
    line-height: 18px;
    color: var(--name-blue);
  }
  .contact__role { margin-bottom: 12px; }
  .contact__address { margin-bottom: 14px; }
  .contact__list { list-style: none; }
  .contact__item { display: flex; align-items: center; gap: 6px; height: 16px; }
  .contact__icon { width: 10px; height: 10px; flex: none; fill: var(--name-blue); }

  /* back: wordmark */
  .back-brand {
    position: absolute;
    left: 88px;
    top: 94px;
    display: flex;
    align-items: center;
    gap: 16px;
  }
  .back-brand__dot {
    width: 84px; height: 84px;
    border-radius: 50%;
    background: var(--card-white);
  }
  .back-brand__name {
    font-family: "Oswald", "Arial Narrow", sans-serif;
    font-weight: 500;
    font-size: 27px;
    line-height: 1.15;
    letter-spacing: 0.5px;
    color: var(--card-white);
    text-transform: uppercase;
  }
</style>
</head>
<body>
  <section class="card card--front" aria-label="Card front">
    <div class="front-brand">
      <div class="front-brand__dot"></div>
      <p class="front-brand__name">Bramblefield<br>Growth Partners</p>
    </div>
    <div class="contact">
      <p class="contact__name">Malcolm Dervaney</p>
      <p class="contact__role">Owner</p>
      <p class="contact__address">58 Quorrin Ct, Elmbridge<br>Vic 3190</p>
      <ul class="contact__list">
        <li class="contact__item">
          <svg class="contact__icon" viewBox="0 0 10 10" aria-hidden="true"><path d="M2 0.5 3.6 2.6 2.7 3.7C3.3 5 4.9 6.6 6.3 7.3L7.4 6.4 9.5 8 8.6 9.5C4.6 9.3 0.7 5.4 0.5 1.4Z"/></svg>
          <span>0418923047</span>
        </li>
        <li class="contact__item">
          <svg class="contact__icon" viewBox="0 0 10 10" aria-hidden="true"><path d="M0.5 2.5H9.5V3.2L5 5.8 0.5 3.2Z M0.5 4.2 5 6.8 9.5 4.2V8H0.5Z"/></svg>
          <span>malcolm@bgp.com.au</span>
        </li>
        <li class="contact__item">
          <svg class="contact__icon" viewBox="0 0 10 10" aria-hidden="true"><circle cx="5" cy="5" r="4.5"/><path d="M3 3.5 5 3 5.5 5 4 6.5 3 5Z M6.5 6 7.5 5.5 7.8 7 6.8 7.8Z" fill="#fff"/></svg>
          <span>bramblefieldgrowth.com.au</span>
        </li>
      </ul>
    </div>
  </section>

  <section class="card card--back" aria-label="Card back">
    <div class="back-brand">
      <div class="back-brand__dot"></div>
      <p class="back-brand__name">Bramblefield<br>Growth Partners</p>
    </div>
  </section>
</body>
</html>
```